Business Card Design for Software Development Company

I am looking for a business card design the incorporates my new logo (attached below).

Key information to include:
Name: Martin Quelbrook
Title: CEO
Email: martin@brightwellcivic.example
Phone: 555-218-9403
Website: www.brightwellcivic.example

NOTE: This design should be easy to edit so that we can order cards for different members of our team.

```html
<!DOCTYPE html>
<html lang="en">
<head>
<meta charset="utf-8">
<title>BrightwellLabs Business Card</title>
<link href="https://fonts.googleapis.com/css2?family=Montserrat:wght@400;600;700&family=Open+Sans:wght@400&display=swap" rel="stylesheet">
<style>
  :root {
    --bg: #2a2d31;
    --card: #1f1f20;
    --white: #ffffff;
    --muted: #d9d9d9;
    --teal: #13a89a;
    --teal-dark: #0e8a7e;
    --red: #a01e24;
    --red-orange: #dc4a26;
    --orange: #ee8424;
    --peach: #f8b36f;
    --sand: #fbc891;
  }
  * { margin: 0; padding: 0; box-sizing: border-box; }
  html, body { width: 1200px; height: 900px; overflow: hidden; }
  body {
    background: var(--bg);
    font-family: "Open Sans", sans-serif;
    display: flex;
    flex-direction: column;
    align-items: center;
    justify-content: center;
    gap: 40px;
  }
  .card {
    position: relative;
    width: 700px;
    height: 400px;
    background: var(--card);
    overflow: hidden;
    box-shadow: 0 12px 30px rgba(0,0,0,.45);
  }

  /* Front */
  .edge-stripe {
    position: absolute; left: 0; top: 0; width: 22px; height: 100%;
    display: flex; flex-direction: column;
  }
  .edge-stripe span { flex: 1; }
  .edge-stripe .s1 { background: var(--teal); }
  .edge-stripe .s2 { background: var(--teal-dark); }
  .edge-stripe .s3 { background: var(--red); }
  .edge-stripe .s4 { background: var(--red-orange); }
  .edge-stripe .s5 { background: var(--orange); }
  .edge-stripe .s6 { background: var(--sand); }
  .edge-stripe .s7 { background: var(--peach); }

  .brand { position: absolute; font-family: "Montserrat", sans-serif; color: var(--white); }
  .brand-name { display: flex; align-items: center; gap: 8px; font-weight: 600; letter-spacing: -0.5px; }
  .brand-dot { background: var(--orange); flex: none; }
  .brand-tagline { font-weight: 600; text-transform: uppercase; text-align: right; letter-spacing: .4px; }

  .front .brand { left: 62px; top: 150px; }
  .front .brand-name { font-size: 34px; }
  .front .brand-dot { width: 14px; height: 14px; }
  .front .brand-tagline { font-size: 6.5px; margin-top: 3px; }

  .divider {
    position: absolute; left: 340px; top: 95px; width: 2px; height: 210px;
    background: var(--teal);
  }
  .person { position: absolute; left: 372px; top: 110px; }
  .person-name {
    font-family: "Montserrat", sans-serif; font-weight: 700; font-size: 25px;
    text-transform: uppercase; letter-spacing: .5px; line-height: 1.1;
  }
  .first-name { color: var(--teal); }
  .last-name { color: var(--orange); }
  .person-title { color: var(--muted); font-size: 15px; margin-top: 2px; }
  .contacts { list-style: none; margin-top: 26px; }
  .contacts li {
    display: flex; align-items: center; gap: 10px;
    color: var(--white); font-size: 14.5px; margin-bottom: 9px;
  }
  .contacts svg { width: 12px; height: 12px; flex: none; }

  /* Back */
  .back-decor {
    position: absolute; left: 0; top: 0; width: 100%; height: 150px;
    background: linear-gradient(100deg, var(--sand) 0%, var(--orange) 35%, var(--red-orange) 60%, var(--red) 80%, var(--teal) 100%);
    clip-path: polygon(0 0, 100% 0, 100% 40%, 0 100%);
  }
  .back .brand { right: 60px; bottom: 90px; }
  .back .brand-name { font-size: 62px; }
  .back .brand-dot { width: 22px; height: 22px; }
  .back .brand-tagline { font-size: 9px; margin-top: 4px; }
</style>
</head>
<body>

  <section class="card front" aria-label="Business card front">
    <div class="edge-stripe">
      <span class="s1"></span><span class="s2"></span><span class="s3"></span>
      <span class="s4"></span><span class="s5"></span><span class="s6"></span><span class="s7"></span>
    </div>

    <div class="brand">
      <div class="brand-name"><span class="brand-dot"></span>BrightwellLabs</div>
      <div class="brand-tagline">A division of Brightwell Civic</div>
    </div>

    <div class="divider"></div>

    <div class="person">
      <h1 class="person-name"><span class="first-name">Martin</span> <span class="last-name">Quelbrook</span></h1>
      <p class="person-title">CEO</p>
      <ul class="contacts">
        <li>
          <svg viewBox="0 0 12 12" aria-hidden="true"><path fill="#fbc891" d="M2.5 1h2l1 2.5-1.3 1a6 6 0 0 0 3.3 3.3l1-1.3L11 7.5v2a1.5 1.5 0 0 1-1.5 1.5A8.5 8.5 0 0 1 1 2.5 1.5 1.5 0 0 1 2.5 1z"/></svg>
          555-218-9403
        </li>
        <li>
          <svg viewBox="0 0 12 12" aria-hidden="true"><rect x="1" y="2.5" width="10" height="7" rx="1" fill="#13a89a"/><path d="M1.5 3l4.5 3.5L10.5 3" stroke="#1f1f20" stroke-width="1" fill="none"/></svg>
          martin@brightwellcivic.example
        </li>
        <li>
          <svg viewBox="0 0 12 12" aria-hidden="true"><circle cx="6" cy="6" r="5" fill="#ee8424"/><path d="M1 6h10M6 1c2 2 2 8 0 10M6 1c-2 2-2 8 0 10" stroke="#1f1f20" stroke-width=".8" fill="none"/></svg>
          www.brightwellcivic.example
        </li>
      </ul>
    </div>
  </section>

  <section class="card back" aria-label="Business card back">
    <div class="back-decor" role="img" aria-label="Brand colour band in sand, orange, red and teal"></div>
    <div class="brand">
      <div class="brand-name"><span class="brand-dot"></span>BrightwellLabs</div>
      <div class="brand-tagline">A division of Brightwell Civic</div>
    </div>
  </section>

</body>
</html>
```